Life and Personal development life coach needs card design

I need a card design that matches the style and design of my website. I'd like to stay in the same color scheme. Please check out my website for ideas. www.loretabrenvik.com
I have had previous designs for this. I am wondering if you have access to those for more ideas??

```html
<!DOCTYPE html>
<html lang="en">
<head>
<meta charset="UTF-8">
<title>Loreta Brenvik – Life Coach Business Card</title>
<link rel="stylesheet" href="https://fonts.googleapis.com/css2?family=Crimson+Text:wght@400;700&display=swap">
<style>
  :root {
    --stage: #e9e9e9;
    --card-dark: #0c0c0c;
    --card-light: #ffffff;
    --lime: #b3d235;
    --cyan: #2bc3e6;
    --ink: #151515;
    --tone-skin: #d6d6d6;
    --tone-light: #a8a8a8;
    --tone-mid: #4a4a4a;
    --tone-dark: #1a1a1a;
    --tone-black: #050505;
  }
  * { margin: 0; padding: 0; box-sizing: border-box; }
  html, body {
    width: 1200px; height: 926px; overflow: hidden;
    background: var(--stage);
    font-family: "Crimson Text", Georgia, serif;
    color: var(--ink);
  }
  .canvas { position: relative; width: 1200px; height: 926px; }
  .card {
    position: absolute; left: 240px; width: 720px; height: 411px;
    overflow: hidden;
    box-shadow: 0 6px 18px rgba(0,0,0,0.18);
  }
  .card--front { top: 40px; background: var(--card-dark); }
  .card--back  { top: 475px; background: var(--card-light); }

  .portrait {
    position: absolute; inset: 0;
    background:
      radial-gradient(ellipse 13% 20% at 27% 24%, var(--tone-skin), transparent 75%),
      radial-gradient(ellipse 22% 14% at 20% 66%, var(--tone-skin), transparent 80%),
      radial-gradient(ellipse 14% 26% at 86% 72%, var(--tone-light), transparent 80%),
      radial-gradient(ellipse 12% 12% at 70% 60%, var(--tone-light), transparent 80%),
      radial-gradient(ellipse 20% 42% at 21% 45%, var(--tone-mid), transparent 80%),
      radial-gradient(ellipse 34% 24% at 52% 66%, var(--tone-dark), transparent 85%),
      linear-gradient(180deg, var(--tone-mid) 0%, var(--tone-dark) 18%, var(--tone-black) 100%);
  }

  .label {
    position: absolute; display: inline-block;
    padding: 0 10px; line-height: 1.15; white-space: nowrap;
    font-weight: 400;
  }
  .label--name {
    left: 400px; top: 68px;
    background: var(--lime); font-size: 36px;
  }
  .label--name strong { font-weight: 700; }
  .label--role {
    left: 400px; top: 113px;
    background: var(--lime); font-size: 18px; letter-spacing: 2px;
    padding: 0 10px;
  }
  .contact { list-style: none; }
  .contact li {
    position: absolute; left: 340px;
    background: var(--cyan); font-size: 23px; padding: 0 10px;
    line-height: 1.25; white-space: nowrap;
  }
  .contact li:nth-child(1) { top: 236px; }
  .contact li:nth-child(2) { top: 272px; }
  .contact li:nth-child(3) { top: 308px; }

  .back-title {
    position: absolute; left: 0; right: 0; top: 118px;
    text-align: center; font-size: 60px; font-weight: 400;
    letter-spacing: 8px;
  }
  .back-tagline {
    position: absolute; left: 0; right: 0; top: 200px;
    text-align: center; font-size: 32px; letter-spacing: 2px;
  }
</style>
</head>
<body>
<main class="canvas">
  <section class="card card--front">
    <div class="portrait" role="img" aria-label="Black and white portrait of the coach in a dark dress reclining on a black leather sofa"></div>
    <h1 class="label label--name">Loreta <strong>Brenvik</strong></h1>
    <p class="label label--role">LIFE COACH</p>
    <ul class="contact">
      <li>P: 555-014-2273</li>
      <li>W: www.loretabrenvik.com</li>
      <li>E: loreta@loretabrenvik.com</li>
    </ul>
  </section>

  <section class="card card--back">
    <h2 class="back-title">LIFE COACH</h2>
    <p class="back-tagline">Discover what is possible today!</p>
  </section>
</main>
</body>
</html>
```